Design the Business card for NetVaultic

Business card required for a professional Cyber Security business.
Company Logo and Icon has already been provided however I would like other options for the logo and icon to compare to. Alternatively, please refine/enhance the image of the logo.icon I have already provided.

If you are going to use the provided logo and icon, I was thinking that the company raised Logo on White background would serve well on the front of the card. See attached. AND, a large company raised stand-alone icon to appear on black background on the back of the card with tagline 'Cyber Risk Management, Governance and Consulting' or 'Cyber Security for your Business' See attached.
Alternatively, provide your own design for the logo and icon.

Target Market(s)

Enterprise, Government, Financial.

Contact Information for Business Card

Tavin Orloweth
Founder and CEO

Email Address
Mobile Number
Website URL
LinkedIn URL

Logo Text

NetVaultic - see attached example of logo

Font styles to use
Other font styles liked:
• Berlin Sans FB

Requirements
Must have
• Clean large and bold icon on the back with tagline.
• Horizontal alignment,
Nice to have
• Round edges.
• Raised Logo/Icon
Should not have
• An unprofessional look and feel.

```html
<!DOCTYPE html>
<html lang="en">
<head>
<meta charset="utf-8">
<title>NetVaultic Business Card</title>
<link href="https://fonts.googleapis.com/css2?family=Signika:wght@400;600&family=Roboto:wght@400&display=swap" rel="stylesheet">
<style>
  :root {
    --backdrop: #5e4231;
    --card-white: #f4f4f4;
    --card-dark: #1b1c1e;
    --brand-blue: #1c78cc;
    --soft-blue: #4a72c8;
    --brand-yellow: #f5b800;
    --text-grey: #555a60;
    --divider: #c9c9c9;
  }
  html, body {
    margin: 0;
    width: 1200px;
    height: 960px;
    overflow: hidden;
    background: var(--backdrop);
  }
  .canvas { position: relative; width: 1200px; height: 960px; }
  .card {
    position: absolute;
    width: 600px;
    height: 342px;
    box-shadow: 0 3px 8px rgba(0,0,0,0.45);
    overflow: hidden;
  }
  .card-front { left: 314px; top: 113px; background: var(--card-white); }
  .card-back { left: 311px; top: 472px; height: 343px; background: var(--card-dark); }

  .brand {
    position: absolute;
    left: 112px; top: 94px;
    display: flex; align-items: center; gap: 18px;
  }
  .brand-dot {
    width: 64px; height: 64px; border-radius: 50%;
    background: var(--brand-blue);
  }
  .brand-name {
    font-family: "Signika", sans-serif;
    font-weight: 600;
    font-size: 52px;
    color: var(--brand-blue);
    line-height: 1;
  }

  .person {
    position: absolute;
    right: 333px; top: 216px;
    text-align: right;
    font-family: "Signika", sans-serif;
  }
  .person-name { font-size: 21px; font-weight: 600; color: var(--brand-blue); line-height: 26px; }
  .person-role { font-size: 14px; color: var(--brand-yellow); line-height: 20px; }

  .divider {
    position: absolute; left: 290px; top: 197px;
    width: 1px; height: 80px; background: var(--divider);
  }

  .contacts {
    position: absolute; left: 312px; top: 198px;
    margin: 0; padding: 0; list-style: none;
    font-family: "Roboto", sans-serif; font-size: 14px; color: var(--text-grey);
  }
  .contacts li { display: flex; align-items: center; height: 19px; }
  .contacts svg { width: 12px; height: 12px; margin-right: 10px; fill: var(--brand-blue); }

  .accent-band { position: absolute; left: 0; bottom: 0; width: 600px; height: 12px; }

  .back-mark {
    position: absolute; left: 0; right: 0; top: 66px;
    display: flex; flex-direction: column; align-items: center; gap: 16px;
  }
  .back-dot { width: 110px; height: 110px; border-radius: 50%; background: var(--soft-blue); }
  .back-name {
    font-family: "Signika", sans-serif; font-weight: 600; font-size: 40px;
    color: var(--soft-blue); line-height: 1;
  }
  .tagline {
    position: absolute; left: 0; right: 0; top: 276px;
    text-align: center;
    font-family: "Signika", sans-serif; font-size: 19px;
  }
  .tagline .lead { color: var(--soft-blue); }
  .tagline .tail { color: var(--brand-yellow); }
</style>
</head>
<body>
<div class="canvas">
  <section class="card card-front">
    <div class="brand">
      <span class="brand-dot"></span>
      <span class="brand-name">NetVaultic</span>
    </div>

    <div class="person">
      <div class="person-name">Tavin Orloweth</div>
      <div class="person-role">Founder &amp; CEO</div>
    </div>

    <div class="divider"></div>

    <ul class="contacts">
      <li><svg viewBox="0 0 12 12"><rect x="2.5" y="0" width="7" height="12" rx="1.5"/><rect x="3.8" y="1.5" width="4.4" height="7.5" fill="#fff"/></svg>555 014 2738</li>
      <li><svg viewBox="0 0 12 12"><rect x="0" y="2" width="12" height="8" rx="1"/><path d="M0.5 2.5 L6 7 L11.5 2.5" stroke="#fff" stroke-width="1.2" fill="none"/></svg>tavin@netvaultic.com</li>
      <li><svg viewBox="0 0 12 12"><circle cx="6" cy="6" r="6"/><path d="M3 3.5 Q5 4 4.5 6 Q6 7 5 10 M7.5 2 Q8 4 9.5 4.5 M8 7 Q9 8 8.5 9.5" stroke="#fff" stroke-width="1" fill="none"/></svg>www.netvaultic.com</li>
      <li><svg viewBox="0 0 12 12"><circle cx="6" cy="6" r="6"/></svg>netvaultic</li>
    </ul>

    <svg class="accent-band" viewBox="0 0 600 12" preserveAspectRatio="none">
      <polygon points="0,0 393,0 389,12 0,12" fill="var(--brand-blue)"/>
      <polygon points="396,0 600,0 600,12 392,12" fill="var(--brand-yellow)"/>
    </svg>
  </section>

  <section class="card card-back">
    <div class="back-mark">
      <span class="back-dot"></span>
      <span class="back-name">NetVaultic</span>
    </div>
    <p class="tagline"><span class="lead">Cyber Risk Management,</span> <span class="tail">Governance &amp; Consulting</span></p>
  </section>
</div>
</body>
</html>
```